Business Card Design

We like to use greens as you will see in our logo (but not TOO much green). We are a Dental Clinic in a somewhat eccentric community. We do not like the dated sharp designs which we see many dentists use. We're looking for something bright and fresh while still maintaining the integrity of the profession. Elegance is not necessarily what we are going for... we need for the design to be "mature" but also up-lifting.

See our logo.
Updates

Project Deadline Extended
Reason: We have 5 designs which we like. But we'd like to see a few more before committing to a design.

Project Deadline Extended
Reason: We are awaiting revisions to this project. We are still welcoming designs while we wait to see if designers are able to provide to us the revisions we require in order to proceed with a selection.

Target Market(s)

Younger families - ages late 20's to early 40's

Industry/Entity Type

Business

Contact Information for Business Card

Corwel T. Banfry DDS 2730 W. Halvert Rd. Ste. 7 Royal Oak, MI 48391 (248)555-0174 FX (248)555-0189 info@BrightwellDentalCareMi.com BrigthwellDentalCareMi.com on the back of the card we need an appointment reminder (For____ Date___ Time____) with "If you are unable to keep your appointment, kindly give 48 hours notice" at the bottom. No use of teeth in the design. DOUBLE SIDED DESIGN

Requirements
Should not have
• The use of pictures of teeth

```html
<!DOCTYPE html>
<html lang="en">
<head>
<meta charset="utf-8">
<title>Brightwell Dental Care – Business Card</title>
<link rel="stylesheet" href="https://fonts.googleapis.com/css2?family=Cinzel:wght@500&family=Source+Sans+3:ital,wght@0,400;0,600;0,700;1,400&display=swap">
<style>
  :root{
    --green-deep:#1f6b33;
    --green-band:#1d6a30;
    --green-light:#a9d66d;
    --ink:#2b2b2b;
    --ink-soft:#3a3a3a;
    --paper:#ffffff;
    --backdrop:#ecebe6;
    --box-line:#555555;
  }
  *{box-sizing:border-box;margin:0;padding:0}
  html,body{width:1200px;height:1183px;overflow:hidden}
  body{background:var(--backdrop);position:relative;font-family:"Source Sans 3",sans-serif;color:var(--ink)}

  .card{position:absolute;background:var(--paper);box-shadow:0 2px 8px rgba(0,0,0,.18)}
  .card--front{left:34px;top:39px;width:941px;height:534px}
  .card--back{left:217px;top:604px;width:941px;height:534px}

  /* brand */
  .brand{position:absolute;display:flex;align-items:center;gap:14px;color:var(--green-deep);font-family:"Source Sans 3",sans-serif;font-weight:600;line-height:1}
  .brand__dot{flex:none;border-radius:50%;background:var(--green-deep)}
  .brand__name{display:block}
  .card--front .brand{left:39px;top:80px}
  .card--front .brand__dot{width:26px;height:26px}
  .card--front .brand__name{font-size:44px}
  .card--front .brand__line{font-size:44px;margin-top:6px}
  .card--back .brand{left:77px;top:50px}
  .card--back .brand__dot{width:18px;height:18px}
  .card--back .brand__name{font-size:31px}
  .card--back .brand__line{font-size:31px;margin-top:4px}

  /* contacts */
  .contacts{position:absolute;left:43px;top:282px;list-style:none}
  .contacts li{display:flex;align-items:center;gap:7px;height:41px;font-size:23px;color:var(--ink)}
  .contacts svg{width:18px;height:18px;flex:none;fill:var(--green-deep)}

  .dentist{position:absolute;right:182px;top:365px;text-align:right}
  .dentist__name{font-size:35px;font-weight:700;color:var(--green-deep);line-height:1.1}
  .dentist__title{font-size:23px;color:var(--ink);margin-top:4px}

  .front-rule{position:absolute;left:0;right:0;top:456px;height:4px;background:var(--green-light)}
  .address{position:absolute;left:43px;top:478px;font-size:23px;color:var(--ink)}

  /* back */
  .appt-title{position:absolute;left:80px;top:174px;font-family:"Cinzel",serif;font-weight:500;font-size:36px;color:var(--green-deep);letter-spacing:.5px}
  .field{position:absolute;left:82px;display:flex;align-items:flex-end;font-size:25px;color:var(--ink-soft)}
  .field__dots{display:inline-block;border-bottom:2px dotted #777;height:1px;margin:0 10px 7px}
  .field--name{top:245px}
  .field--date{top:312px}
  .next-label{position:absolute;left:82px;top:383px;font-size:26px;color:var(--ink-soft)}
  .next-box{position:absolute;top:382px;width:170px;height:38px;border:2px solid var(--box-line);border-radius:6px}
  .next-box--a{left:336px}
  .next-box--b{left:542px}

  .days{position:absolute;right:26px;top:0;list-style:none}
  .days li{position:absolute;right:0;display:flex;align-items:center;gap:14px;font-size:25px;font-weight:600;color:var(--ink)}
  .days span.box{display:block;width:58px;height:34px;border:2px solid var(--box-line);border-radius:5px}

  .notice{position:absolute;left:78px;top:458px;font-size:26px;font-style:italic;color:var(--ink)}
  .back-band{position:absolute;left:0;right:0;bottom:0;height:11px;background:var(--green-band)}
</style>
</head>
<body>

<section class="card card--front" aria-label="Business card front">
  <div class="brand">
    <span class="brand__dot"></span>
    <span><span class="brand__name">Brightwell</span><span class="brand__name brand__line">Dental Care</span></span>
  </div>

  <ul class="contacts">
    <li><svg viewBox="0 0 20 20"><path d="M5 2l3 4-2 2c1 2 3 4 5 5l2-2 4 3-2 3C9 17 3 11 2 4z"/></svg>(248)555-0174</li>
    <li><svg viewBox="0 0 20 20"><rect x="5" y="2" width="10" height="5"/><rect x="2" y="8" width="16" height="7" rx="1"/><rect x="5" y="13" width="10" height="5" fill="#fff" stroke="#1f6b33" stroke-width="1.5"/></svg>(248)555-0189</li>
    <li><svg viewBox="0 0 20 20"><rect x="2" y="4" width="16" height="12" rx="2"/><path d="M3 5l7 6 7-6" fill="none" stroke="#fff" stroke-width="1.6"/></svg>info@BrightwellDentalCareMi.com</li>
    <li><svg viewBox="0 0 20 20"><circle cx="10" cy="10" r="8"/><path d="M2 10h16M10 2c-4 4-4 12 0 16M10 2c4 4 4 12 0 16" fill="none" stroke="#fff" stroke-width="1.2"/></svg>BrigthwellDentalCareMi.com</li>
  </ul>

  <div class="dentist">
    <p class="dentist__name">Corwel T. Banfry</p>
    <p class="dentist__title">DDS</p>
  </div>

  <div class="front-rule"></div>
  <p class="address">2730 W. Halvert Rd. Ste. 7 Royal Oak, MI 48391</p>
</section>

<section class="card card--back" aria-label="Business card back, appointment reminder">
  <div class="brand">
    <span class="brand__dot"></span>
    <span><span class="brand__name">Brightwell</span><span class="brand__name brand__line">Dental Care</span></span>
  </div>

  <h2 class="appt-title">YOUR APPOINTMENT</h2>

  <p class="field field--name">Name :<span class="field__dots" style="width:520px"></span></p>
  <p class="field field--date">Date :<span class="field__dots" style="width:170px;margin-left:40px"></span>Time :<span class="field__dots" style="width:160px;margin-right:2px"></span>am / pm</p>

  <p class="next-label">Next Appointment</p>
  <span class="next-box next-box--a"></span>
  <span class="next-box next-box--b"></span>

  <ul class="days">
    <li style="top:79px">MON<span class="box"></span></li>
    <li style="top:142px">TUE<span class="box"></span></li>
    <li style="top:207px">WED<span class="box"></span></li>
    <li style="top:274px">THU<span class="box"></span></li>
    <li style="top:333px">FRI<span class="box"></span></li>
    <li style="top:389px">SAT<span class="box"></span></li>
  </ul>

  <p class="notice">If you are unable to keep your appointment, kindly give 48 hours notice</p>
  <div class="back-band"></div>
</section>

</body>
</html>
```